Brochure for a website accessibility report

This brochure is related to a report that www.qelvantrix.org sell. The report shows the results of an automated audit of a websites accessibility. It shows details of issues found with screen shots, examples of code and provides remediation advice.

The brochure will be a pdf 8.5 inches by 11 inches. It can be anywhere from 6 to 10 pages.

The FlintVue™ name itself should be “Bree Serif” font. The fonts, styles, colors and sizes are up to you.

The images used and logo of the Office of Digital Reachworks and K7P logo are upload

We highlighted in blue page extracts from the report we sell. Do not use the blue highlight, it is merely there to show you where the specific examples of the report we sell are vs the other content in the report. The areas in blue which show the content from the actual report should be shown as an extract of the actual page of the report. You have flexibility to change the layout and the way the content look.

The red square callouts over the blue content are callouts that describe the specific page extracts. We used it as a red callout only so that you would be able to see it. You should change the specific location, look and feel of the callout to be appropriate

Target Market(s)

Marketing and Technical people

Industry/Entity Type

Information Technology

Font styles to use
Sans Serif

Colors

Designer to choose colors to be used in the design.

Requirements
Should not have
• wheelchairs, images of blind people

```html
<!DOCTYPE html>
<html lang="en">
<head>
<meta charset="utf-8">
<title>FlintVue™ — Office of Digital Reachworks</title>
<link rel="stylesheet" href="https://fonts.googleapis.com/css2?family=Source+Sans+3:wght@600&display=swap">
<style>
  :root {
    --bg-white: #ffffff;
    --bg-mist: #e6f1f5;
    --bg-glow: #9fd8ee;
    --ink: #1d2b33;
    --shadow: rgba(30, 80, 110, 0.25);
  }
  * { box-sizing: border-box; margin: 0; padding: 0; }
  html, body { width: 1200px; height: 927px; overflow: hidden; }
  body { background: var(--bg-white); }

  .cover {
    position: relative;
    width: 1200px;
    height: 927px;
    overflow: hidden;
    background:
      radial-gradient(ellipse 520px 420px at 230px 420px, var(--bg-glow) 0%, rgba(159,216,238,0.35) 45%, rgba(255,255,255,0) 75%),
      linear-gradient(100deg, var(--bg-mist) 0%, var(--bg-white) 55%, var(--bg-mist) 100%);
  }
  .cover__rays { position: absolute; inset: 0; pointer-events: none; }

  .collage { position: absolute; inset: 0; }
  .collage__tile {
    position: absolute;
    box-shadow: 0 6px 18px var(--shadow);
    transform: perspective(900px) rotateY(14deg);
    transform-origin: left center;
  }
  .tile--laptop    { left: 0;     top: 53px;  width: 114px; height: 197px; background: linear-gradient(135deg, #2f7fc4, #a9dcf2); }
  .tile--globe     { left: 242px; top: 58px;  width: 159px; height: 139px; background: linear-gradient(135deg, #1f73b8, #d9f1fb); }
  .tile--autumn    { left: 118px; top: 155px; width: 253px; height: 171px; background: linear-gradient(160deg, #d7a62c, #7c8a2e 70%, #c9b58a); }
  .tile--sunflower { left: 412px; top: 129px; width: 206px; height: 162px; background: linear-gradient(135deg, #f2a516, #f7d23a 60%, #7fae3a); }
  .tile--coast     { left: 0;     top: 341px; width: 220px; height: 114px; background: linear-gradient(180deg, #bfe3f1, #4aa7c8 60%, #c98d5a); }
  .tile--worldmap  { left: 323px; top: 333px; width: 225px; height: 167px; background: linear-gradient(135deg, #0c4f8f, #3fa6dc 60%, #bde6f6); }
  .tile--monitor   { left: 503px; top: 273px; width: 186px; height: 167px; background: linear-gradient(135deg, #f6f2b0, #bfe27a 50%, #ffffff); }
  .tile--droplet   { left: 0;     top: 474px; width: 45px;  height: 162px; background: linear-gradient(180deg, #6cc23a, #2d8a2a); }
  .tile--hands     { left: 83px;  top: 420px; width: 277px; height: 171px; background: linear-gradient(135deg, #e7c4ad, #c08f75 55%, #f4ede6); }
  .tile--roses     { left: 412px; top: 477px; width: 204px; height: 147px; background: linear-gradient(135deg, #2f6b2a, #d8325e 55%, #3f7a30); }
  .tile--child     { left: 545px; top: 541px; width: 167px; height: 163px; background: linear-gradient(135deg, #e0403d, #c92a2f 60%, #f08a6a); }
  .tile--houses    { left: 189px; top: 583px; width: 223px; height: 91px;  background: linear-gradient(180deg, #eef4f6, #8fbf6a 70%, #4f8f3a); }
  .tile--sparkle   { left: 0;     top: 621px; width: 295px; height: 167px; background: linear-gradient(135deg, #0a2f7a, #1d7fd0 55%, #7fd3f5); }
  .tile--hearttree { left: 321px; top: 655px; width: 224px; height: 186px; background: linear-gradient(180deg, #7cc1ea, #cfe9f7 55%, #6fb04a); }

  .org-name {
    position: absolute;
    left: 800px;
    top: 100px;
    width: 320px;
    font-family: "Source Sans 3", sans-serif;
    font-weight: 600;
    font-size: 30px;
    line-height: 38px;
    color: var(--ink);
  }

  .product {
    position: absolute;
    left: 764px;
    top: 778px;
    font-family: "Source Sans 3", sans-serif;
    font-weight: 600;
    font-size: 60px;
    line-height: 1;
    color: var(--ink);
  }
</style>
</head>
<body>
  <main class="cover">
    <svg class="cover__rays" width="1200" height="927" viewBox="0 0 1200 927" aria-hidden="true">
      <polygon points="0,300 1200,120 1200,200 0,420" fill="#ffffff" opacity="0.35"/>
      <polygon points="0,560 1200,420 1200,470 0,640" fill="#ffffff" opacity="0.3"/>
      <polygon points="0,700 1200,620 1200,700 0,800" fill="#dff0f6" opacity="0.4"/>
    </svg>

    <section class="collage">
      <div class="collage__tile tile--laptop" role="img" aria-label="Photo of a laptop with a glowing screen"></div>
      <div class="collage__tile tile--autumn" role="img" aria-label="Photo of autumn trees in a park"></div>
      <div class="collage__tile tile--globe" role="img" aria-label="Photo of a digital globe"></div>
      <div class="collage__tile tile--sunflower" role="img" aria-label="Close-up photo of a yellow flower"></div>
      <div class="collage__tile tile--coast" role="img" aria-label="Photo of a small island village by the sea"></div>
      <div class="collage__tile tile--monitor" role="img" aria-label="Illustration of a computer monitor and globe"></div>
      <div class="collage__tile tile--worldmap" role="img" aria-label="Illustration of a glowing world map"></div>
      <div class="collage__tile tile--droplet" role="img" aria-label="Photo of water drops on a green leaf"></div>
      <div class="collage__tile tile--hands" role="img" aria-label="Photo of two hands holding each other"></div>
      <div class="collage__tile tile--roses" role="img" aria-label="Photo of pink roses"></div>
      <div class="collage__tile tile--child" role="img" aria-label="Photo of a child in red holding a heart"></div>
      <div class="collage__tile tile--houses" role="img" aria-label="Photo of houses on a green lawn"></div>
      <div class="collage__tile tile--sparkle" role="img" aria-label="Abstract blue light streaks"></div>
      <div class="collage__tile tile--hearttree" role="img" aria-label="Photo of a heart-shaped tree under a blue sky"></div>
    </section>

    <p class="org-name">Office of Digital Reachworks</p>

    <h1 class="product">FlintVue™</h1>
  </main>
</body>
</html>
```